LIFE CHANGING NEW WEBSITE DESIGN NEEDED FOR FULL WEBSITE- FUN/FEMININE!

I need a website designed for a personal financial advice website geared at women called BLUE OTTER LANTERN. I will be providing free financial advice around topics of making, saving, spending and sharing money. The concept is to change the way women understand money and the necessity around building various passive income streams to ensure full financial freedom. This will then carry down to advice for mothers with children and children in particular. The website should be elegant and yet witty. I don't want lots of serious photos but more relatable. I will have a photo of myself and my story as this is a blog and needs to be relatable to women and mothers. I like pinks and greys. I want to have a pink piggy bank being broken with a hammer in the front screen to break our traditional mindset around piggy bank saving/spending habits. I have created a logo that is a pink piggy head with BLUE OTTER LANTERN that needs to be incorporated so that it blends into the heading. I have also already started designing the website on Squarespace and can provide access to that. Basically it should have a format of BLUE OTTER LANTERN LOGO center in header then on left hand navigation: MAKE, SAVE, SPEND, SHARE then on right hand header navigation: MISSION, GET STARTED, CONTACT BOL I would like to have the front page when you go to the url to have the image of the piggy bank being broken then a catchy phrase then under 4 boxes with MAKE (image and description) SAVE (image and description) SPEND (image and description) SHARE (image and description) if you click on those or the title they go to pages that are dedicated to each them. Each page should have a little intro on the topic then I want lots of blog links as I will be mainly writing blogs. Each blog site should have ability to write comments as well. I need social media icons on each page too. Please let me know what you need from me to get started. I prefer having a discussion if possible to not waste anyone's time. I need the site to be easy for me to use and add blogs/urls etc as needed. I also need the site to be put into my domain that I already purchased: www.blueotterlantern-sample.com

Target Market(s)

teenage girls, 20 something girls, 30 something girls and mothers

Coding

Coded - Design and coding required

Number of Pages Required

5+ page

Font styles to use
Sans Serif

Colors
e667a6
e34197
f59195
eea4c8
aaaaaa
cbcbcb
959595

Requirements
Must have
• TOP NAVIGATION
• MAKE SAVE SPEND SHARE LOGO/BLUE OTTER LANTERN MISSION GET STARTED CONTACT BOL
• FRONT PAGE: IMAGE OF PIGGY BANK BEING BROKEN WITH A HAMMER
• CATCH PHRASE OVER THE IMAGE
• BUTTON IN PINK- TAKE ACTION (WHICH DIRECTS TO TAKE ACTION TAB ON NAVIGATION HEADER
• 4 BOXES BELOW MAIN IMAGE WITH IMAGE/DESCRIPTIONS FOR MAKE, SAVE, SPEND, SHARE THAT EACH GO TO THE PAGES FROM THE NAVIGATION HEADER
• EACH PAGE SHOULD BE DEDICATED TO THOSE TOPICS THEN THERE IS AN INTRO ON EACH PAGE THEN THE LINKS TO DIFFERENT BLOGS AROUND EACH TOPIC FOR MAKE, SAVE, SPEND, SHARE
• EACH BLOG SHOULD HAVE COMMENTS SECTION AND SOCIAL MEDIA ICONS
• (GOOD TO USE PINKS/GREYS)
Should not have
• BE SUPER BUSY, CLUTTERED, FEEL LIKE I AM SELLING SOMETHING

```html
<!DOCTYPE html>
<html lang="en">
<head>
<meta charset="utf-8">
<title>Blue Otter Lantern</title>
<link rel="stylesheet" href="https://fonts.googleapis.com/css2?family=Nunito:wght@400;600;700&family=Lato:wght@400;700&display=swap">
<style>
:root{
  --pink-deep:#e34197;
  --pink:#e667a6;
  --pink-soft:#eea4c8;
  --salmon:#f59195;
  --link:#ea6f7e;
  --grey-light:#e9e9e9;
  --grey-mid:#cbcbcb;
  --grey:#959595;
  --grey-dark:#8a8a8a;
  --text:#555;
  --ink:#333;
  --white:#fff;
}
*{box-sizing:border-box;margin:0;padding:0}
html,body{width:1200px;height:2434px;overflow:hidden;background:var(--white)}
body{position:relative;font-family:'Lato',sans-serif;color:var(--text)}
.abs{position:absolute}
a{text-decoration:none;color:inherit}

/* header */
.site-nav{position:absolute;top:34px;font-family:'Nunito',sans-serif;font-size:16px;font-weight:600;color:var(--grey);letter-spacing:.2px}
.site-nav a{position:absolute;white-space:nowrap}
.brand-tab{position:absolute;left:466px;top:0;width:268px;height:127px;z-index:3}
.brand{position:absolute;left:0;top:68px;width:268px;text-align:center;font-family:'Nunito',sans-serif;font-size:25px;font-weight:600;color:var(--pink-deep);z-index:4}
.brand-dot{position:absolute;left:578px;top:20px;width:44px;height:44px;border-radius:50%;border:3px solid var(--pink);z-index:4}

/* hero */
.hero{position:absolute;left:0;top:85px;width:1200px;height:720px;overflow:hidden}
.hero-bg{position:absolute;inset:0;background:linear-gradient(100deg,#d9187a 0%,#ec3b8d 35%,#ef75ad 65%,#eea4c8 100%)}
.hero-photo{position:absolute;left:620px;top:0;width:420px;height:640px;background:linear-gradient(180deg,#f2d28a 0%,#f3a7c0 30%,#4a7fc9 60%,#3b6bb5 100%);opacity:.55}
.hero-curve{position:absolute;left:0;top:0}
.hero-copy{position:absolute;left:120px;top:198px;width:500px;text-align:center;color:var(--white);font-family:'Nunito',sans-serif;font-weight:600}
.hero-copy .lead{font-size:42px;line-height:48px}
.hero-copy h1{font-size:50px;line-height:60px;font-weight:700}
.btn{display:inline-block;text-align:center;font-family:'Nunito',sans-serif;font-weight:600;color:var(--white);border-radius:30px;text-transform:uppercase}
.btn-hero{position:absolute;left:275px;top:318px;width:191px;height:55px;line-height:55px;background:var(--salmon);font-size:17px}
.hero-arrow{position:absolute;top:243px}

/* topic cards */
.card{position:absolute;top:567px;width:219px;height:335px;background:var(--white);border:1px solid var(--grey-mid);text-align:center;z-index:2}
.card-media{height:167px;width:100%}
.card h2{margin-top:17px;font-family:'Nunito',sans-serif;font-size:22px;font-weight:600;color:var(--pink-deep)}
.card p{margin:8px auto 0;width:190px;font-size:12.5px;line-height:16.5px;color:var(--text)}
.card .btn{position:absolute;left:44px;top:280px;width:130px;height:38px;line-height:38px;background:var(--pink-deep);font-size:13px}

/* mission */
.mission-bg{position:absolute;left:0;top:955px}
.mission-photo{position:absolute;left:0;top:1025px;width:605px;height:511px;background:linear-gradient(120deg,#e3e3e3 0%,#bfe0dc 40%,#f1c3da 80%,#e6e6e6 100%)}
.mission-copy{position:absolute;left:612px;top:1113px;width:475px}
.mission-copy h2{font-family:'Nunito',sans-serif;font-size:36px;font-weight:600;color:#4a4a4a;margin-bottom:16px}
.mission-copy p{font-size:16px;line-height:21.7px;color:var(--text);margin-left:3px;margin-bottom:24px}
.btn-mission{position:absolute;left:615px;top:1375px;width:164px;height:47px;line-height:47px;background:var(--pink-deep);font-size:15px}

/* blogs */
.blogs-title{position:absolute;left:163px;top:1640px;font-family:'Nunito',sans-serif;font-size:36px;font-weight:600;color:var(--pink-deep)}
.feature-media{position:absolute;left:163px;top:1704px;width:428px;height:243px;background:linear-gradient(90deg,#bdbdbd 0%,#e2b6cf 45%,#5a3a2c 75%,#2d2d2d 100%)}
.meta{font-size:14px;color:var(--ink)}
.post-title{font-family:'Lato',sans-serif;font-weight:700;text-transform:uppercase;color:var(--ink);letter-spacing:-.2px}
.read-more{font-family:'Nunito',sans-serif;font-size:16px;font-weight:600;color:var(--link)}
.feature{position:absolute;left:172px;top:1973px;width:420px}
.feature .post-title{font-size:18.5px;line-height:24px;margin-top:9px}
.feature .excerpt{font-size:13px;line-height:21px;margin-top:9px;color:#444}
.feature .read-more{display:block;margin-top:10px}
.post-item{position:absolute;left:632px;width:417px;height:160px}
.post-item .thumb{position:absolute;left:0;top:0;width:129px;height:118px}
.post-item .body{position:absolute;left:157px;top:8px;width:270px}
.post-item .post-title{font-size:17.5px;line-height:23px;margin-top:6px}
.post-item .read-more{display:block;margin-top:10px}
.divider{position:absolute;left:632px;width:417px;height:1px;background:var(--grey-mid)}

/* footer */
.footer-bg{position:absolute;left:0;top:2170px}
.footer-nav{position:absolute;top:2300px;left:0;width:1200px;text-align:center;font-family:'Nunito',sans-serif;font-size:16px;font-weight:600;color:var(--white)}
.footer-nav a{margin:0 13px}
.copyright{position:absolute;top:2331px;left:0;width:1200px;text-align:center;font-size:13px;color:var(--white)}
.social{position:absolute;top:2373px;left:490px;width:220px;display:flex;justify-content:space-between}
.social a{width:22px;height:22px;border-radius:50%;border:2px solid var(--white)}
</style>
</head>
<body>

<!-- header -->
<nav class="site-nav" aria-label="Topics">
  <a href="#" style="left:99px">MAKE</a>
  <a href="#" style="left:179px">SAVE</a>
  <a href="#" style="left:255px">SPEND</a>
  <a href="#" style="left:345px">SHARE</a>
</nav>
<nav class="site-nav" aria-label="About">
  <a href="#" style="left:770px">MISSION</a>
  <a href="#" style="left:873px">GET STARTED</a>
  <a href="#" style="left:1020px">CONTACT BOL</a>
</nav>

<!-- hero -->
<section class="hero">
  <div class="hero-bg"></div>
  <div class="hero-photo" role="img" aria-label="Smiling woman in glasses dropping a coin into a pink piggy bank"></div>
  <svg class="hero-curve" width="1200" height="720" viewBox="0 0 1200 720">
    <path d="M0 633 Q600 520 1200 620 L1200 720 L0 720 Z" fill="#fff"/>
  </svg>
  <div class="hero-copy">
    <div class="lead">Welcome to</div>
    <h1>Blue Otter Lantern</h1>
  </div>
  <a href="#" class="btn btn-hero">Take Action</a>
  <svg class="hero-arrow" style="left:58px" width="30" height="52" viewBox="0 0 30 52"><path d="M26 2 L4 26 L26 50" fill="none" stroke="#fff" stroke-width="2.5"/></svg>
  <svg class="hero-arrow" style="left:1100px" width="30" height="52" viewBox="0 0 30 52"><path d="M4 2 L26 26 L4 50" fill="none" stroke="#fff" stroke-width="2.5"/></svg>
</section>

<svg class="brand-tab" viewBox="0 0 268 127"><path d="M0 85 Q28 85 30 100 Q40 127 80 127 L188 127 Q228 127 238 100 Q240 85 268 85 L268 0 L0 0 Z" fill="#fff"/></svg>
<span class="brand-dot" aria-hidden="true"></span>
<div class="brand abs" style="left:466px">Blue Otter Lantern</div>

<!-- topic cards -->
<article class="card" style="left:150px">
  <div class="card-media" role="img" aria-label="Hands on a laptop keyboard with banknotes flying out" style="background:linear-gradient(135deg,#d8cfc8,#8a8a86 60%,#4f5a4c)"></div>
  <h2>MAKE</h2>
  <p>Lorem ipsum dolor sit amet consectetuer adipiscing elit Nam cursus Morbi ut mi Nullam</p>
  <a href="#" class="btn">Click Here</a>
</article>
<article class="card" style="left:384px">
  <div class="card-media" role="img" aria-label="Pink piggy bank on a table" style="background:linear-gradient(135deg,#ede4e0,#f1c0c6 50%,#d7c7c2)"></div>
  <h2>SAVE</h2>
  <p>Lorem ipsum dolor sit amet consectetuer adipiscing elit Nam cursus Morbi ut mi Nullam</p>
  <a href="#" class="btn">Click Here</a>
</article>
<article class="card" style="left:617px">
  <div class="card-media" role="img" aria-label="Woman in sunglasses carrying shopping bags" style="background:linear-gradient(135deg,#e8b064,#c9876a 45%,#f0d28a)"></div>
  <h2>SPEND</h2>
  <p>Lorem ipsum dolor sit amet consectetuer adipiscing elit Nam cursus Morbi ut mi Nullam</p>
  <a href="#" class="btn">Click Here</a>
</article>
<article class="card" style="left:851px">
  <div class="card-media" role="img" aria-label="Woman working on a laptop at home" style="background:linear-gradient(135deg,#cfcfcf,#5a9aa0 50%,#bcbcbc)"></div>
  <h2>SHARE</h2>
  <p>Lorem ipsum dolor sit amet consectetuer adipiscing elit Nam cursus Morbi ut mi Nullam</p>
  <a href="#" class="btn">Click Here</a>
</article>

<!-- mission -->
<svg class="mission-bg" width="1200" height="690" viewBox="0 0 1200 690">
  <path d="M0 20 Q300 70 614 72 Q900 60 1200 30 L1200 680 Q900 620 614 585 Q300 600 0 660 Z" fill="#e8e8e8"/>
  <path d="M614 73 Q900 60 1200 9" fill="none" stroke="#e34197" stroke-width="4"/>
  <path d="M0 672 Q300 600 614 585" fill="none" stroke="#e34197" stroke-width="5"/>
</svg>
<div class="mission-photo" role="img" aria-label="Smiling woman with curly hair putting a coin into a large pink piggy bank"></div>
<div class="mission-copy">
  <h2>Our Mission</h2>
  <p>My mission is simple- I want to challenge you to rethink the way you think about growing, spending and saving money. By redesigning your life around your finances I want you to run your life as if you are the CEO of your own business, and the business is maximising the value and profitability of your life.</p>
  <p>It is shocking that in today's world of information we are we still live in a society where most educated people leave school</p>
</div>
<a href="#" class="btn btn-mission">Learn More</a>

<!-- recent blogs -->
<h2 class="blogs-title">Recent Blogs</h2>
<div class="feature-media" role="img" aria-label="Smiling woman holding a pink piggy bank stuffed with banknotes"></div>
<article class="feature">
  <div class="meta">April 12, 2019 &nbsp;|&nbsp; No Comments</div>
  <h3 class="post-title">Mauris vel lacus vitae felis vestibulum volutpat etiam est nunc</h3>
  <p class="excerpt">Nunc tempus felis vitae urna Vivamus porttitor neque at volutpat rutrum purus nisi eleifend libero a tempus libero lectus</p>
  <a href="#" class="read-more">Learn More</a>
</article>

<article class="post-item" style="top:1704px">
  <div class="thumb" role="img" aria-label="Hand dropping a coin into a white piggy bank" style="background:linear-gradient(135deg,#c98a3e,#ece6df 55%,#b56a2a)"></div>
  <div class="body">
    <div class="meta">April 08, 2019 &nbsp;|&nbsp; No Comments</div>
    <h3 class="post-title">Mauris vel lacus vitae felis vestibulum volutpat</h3>
    <a href="#" class="read-more">Learn More</a>
  </div>
</article>
<div class="divider" style="top:1840px"></div>
<article class="post-item" style="top:1864px">
  <div class="thumb" role="img" aria-label="Cupped hands holding a white piggy bank" style="background:linear-gradient(135deg,#5f8d9a,#eee9e2 50%,#6e95a1)"></div>
  <div class="body">
    <div class="meta">April 06, 2019 &nbsp;|&nbsp; No Comments</div>
    <h3 class="post-title">Fusce tellus sed metus augue convallis et</h3>
    <a href="#" class="read-more">Learn More</a>
  </div>
</article>
<div class="divider" style="top:2003px"></div>
<article class="post-item" style="top:2023px">
  <div class="thumb" role="img" aria-label="Mother and daughter saving coins in a piggy bank" style="background:linear-gradient(135deg,#b48c6e,#f1e4dc 50%,#6b4a3a)"></div>
  <div class="body">
    <div class="meta">April 02, 2019 &nbsp;|&nbsp; No Comments</div>
    <h3 class="post-title">Phasellus felis dolor scelerisque a tempus</h3>
    <a href="#" class="read-more">Learn More</a>
  </div>
</article>

<!-- footer -->
<svg class="footer-bg" width="1200" height="264" viewBox="0 0 1200 264">
  <path d="M0 7 Q600 110 1200 7 L1200 264 L0 264 Z" fill="#8a8a8a"/>
  <circle cx="602" cy="67" r="34" fill="#fff"/>
  <circle cx="602" cy="66" r="17" fill="none" stroke="#e667a6" stroke-width="3"/>
</svg>
<nav class="footer-nav" aria-label="Footer">
  <a href="#">MAKE</a><a href="#">SAVE</a><a href="#">SPEND</a><a href="#">SHARE</a><a href="#">MISSION</a><a href="#">GET STARTED</a><a href="#">CONTACT BOL</a>
</nav>
<p class="copyright">© 2019 Company Name &nbsp;All right reserved</p>
<div class="social" aria-label="Social links">
  <a href="#" aria-label="Social profile one"></a>
  <a href="#" aria-label="Social profile two"></a>
  <a href="#" aria-label="Social profile three"></a>
  <a href="#" aria-label="Social profile four"></a>
</div>

</body>
</html>
```